High-end Oceanfront Real Estate Group Needs Clean, Modern Web Design

I’m looking for a clean, professional, modern and beautiful homepage web design for a Real Estate group in Southern California, USA.

The group/company is “Marwick on the Shore,” and they specialize in high end (i.e. expensive), oceanfront real estate in the Orange County area.

The look and feel of the page should accentuate the brand qualities: luxurious/expensive, professional, and beautiful (Orange County is one of the most beautiful areas in all the US and we would love the site to emphasize the beautiful beaches and scenery it has to offer).

Looks we like:
• www.brantleyhomesrealty.example
• www.closedbyvane.example -- I think the design is pretty out-dated in this site, but I like the organization/layout of the site

Header Tags (I don’t know if we can fit all of these, may need a side-menu, but I’d prefer header title only if possible):
• Welcome
• Featured Listings
• Previously Sold
• Sell
• Property Search
• Team
• Videos
• Blog
• Explore O.C.
• Contact

I have attached the beach and logo pics that we would like to use as the header, a few pictures of the team, and one sample home/view pic which can be used in any of the other sections (for pictures of the homes, just find expensive oceanfront houses and that will be fine).

I promise to provide feedback to each and every design submission. I appreciate the hard work that all of you are putting into your designs. There can be only one contest winner, but I hope to give all of you helpful feedback to submit the best designs possible!

Target Market(s)

Very wealthy home owners of oceanfront properties. These properties are worth several millions of dollars, and thus the site and brand needs to be targeted to very wealthy, successful individuals and families (both US and international buyers).

Industry/Entity Type

Real Estate

Number of Pages Required

2 page

Requirements
Must have
• I don’t want to give too many requirements, because I want to let you all be creative. However, here are the few Must Haves:
• Must submit 2 page designs (a home page and a sub page)
• Must use logo provided
• Focus is mostly on homes, but I would like to include some beach/ocean imagery as well
• The first “item” on the home page should be an accordion/slider which shows pictures of homes and with 1 line of text: “List with the Leader” and two link buttons: “Sell Your Home” and “Buy Your Home”
• Color palette needs to be mainly blues--to match ocean and sky blue
• Exported in all major formats (psd,ai,eps,png,jpeg,etc)
Nice to have
• We don’t necessarily need all of these, but would like to feature most:
• List of videos
• “Meet the Team”—brief team bios and pics
• Link(s) to Blog
• “List with the Leader” – section on why they should choose this firm
• Featured Listings
• Previously Sold

```html
<!DOCTYPE html>
<html lang="en">
<head>
<meta charset="utf-8">
<title>Marwick on the Shore — Oceanfront Real Estate</title>
<link rel="stylesheet" href="https://fonts.googleapis.com/css2?family=Source+Sans+3:ital,wght@0,300;0,400;0,600;1,400&family=Open+Sans:ital,wght@0,400;0,600;1,400&display=swap">
<style>
:root{
  --ocean:#24a2d3;
  --ocean-deep:#1b8dbd;
  --logo-blue:#2aaedb;
  --leaf:#6cc52b;
  --leaf-deep:#5db321;
  --ink:#3a3a3a;
  --muted:#8a8a8a;
  --mist:#efefef;
  --white:#ffffff;
  --line:#d9d9d9;
  --display:"Source Sans 3",Arial,sans-serif;
  --body:"Open Sans",Arial,sans-serif;
}
*{box-sizing:border-box;margin:0;padding:0}
html,body{width:1200px;height:3364px;overflow:hidden}
body{font-family:var(--body);color:var(--ink);background:var(--white);position:relative}
section,header,footer{position:relative;width:1200px;overflow:hidden}
.section-title{font-family:var(--display);font-weight:300;font-size:25px;letter-spacing:.5px;text-transform:uppercase;text-align:center}
.title-rule{width:74px;height:2px;margin:14px auto 0;background:currentColor;opacity:.7}
.btn{display:inline-block;font-family:var(--body);font-size:10.5px;font-weight:600;letter-spacing:1.5px;text-transform:uppercase;text-align:center;text-decoration:none}
.btn-green{background:var(--leaf);color:var(--white)}
.btn-ghost{border:1.5px solid rgba(255,255,255,.75);color:var(--white)}
.lede{font-size:10.5px;line-height:18px;text-align:center}

/* hero */
.hero{height:422px}
.hero-photo{position:absolute;inset:0;background:linear-gradient(180deg,#a9b8c6 0%,#8a8079 22%,#6d5f55 42%,#5e6e3c 60%,#3f6b22 74%,#6a8a3a 86%,#8f8f84 100%)}
.nav{position:absolute;top:0;left:0;width:1200px;height:58px;background:rgba(255,255,255,.93)}
.nav a{position:absolute;top:23px;font-family:var(--body);font-size:11.5px;color:#444;text-decoration:none;text-transform:uppercase}
.brand{position:absolute;left:516px;top:0;width:168px;height:117px;background:var(--white);display:flex;align-items:center;justify-content:center;text-align:center;font-family:var(--display);font-weight:300;font-size:29px;line-height:30px;color:var(--logo-blue)}
.dropdown{position:absolute;left:929px;top:45px;width:121px;height:117px;background:var(--white);box-shadow:0 2px 6px rgba(0,0,0,.2);padding:10px 0 0 12px}
.dropdown span{display:block;font-size:9.5px;color:#444;line-height:26px;text-transform:uppercase;border-bottom:1px solid #eee;margin-right:12px}
.hero-line{position:absolute;top:188px;width:100%;text-align:center;font-family:var(--display);font-weight:300;font-size:50px;letter-spacing:1px;color:var(--white);text-transform:uppercase}
.hero-actions{position:absolute;top:276px;left:442px}
.hero-actions .btn{height:34px;line-height:34px;width:155px;float:left}
.hero-actions .btn-blue{background:var(--ocean);color:var(--white);margin-left:9px;width:152px}
.dots{position:absolute;top:380px;left:580px;display:flex;gap:6px}
.dots i{width:10px;height:10px;border-radius:50%;background:var(--white)}
.dots i.on{background:var(--ocean)}

/* welcome */
.welcome{height:264px;background:var(--ocean);color:var(--white);padding-top:40px}
.welcome .lede{width:800px;margin:30px auto 0}
.welcome .btn{display:block;margin:26px auto 0;width:152px;height:38px;line-height:36px}

/* listings */
.listings{height:516px;background:var(--mist);padding-top:40px}
.tabs{display:flex;justify-content:center;gap:32px;font-family:var(--display);font-weight:300;font-size:25px;text-transform:uppercase}
.tab{padding-bottom:14px;border-bottom:2px solid #777;color:#555}
.tab.active{color:var(--leaf);border-color:var(--leaf)}
.cards{position:absolute;top:122px;left:200px;display:flex;gap:51px}
.card{width:232px;height:275px;background:var(--white);text-align:center}
.card-photo{height:147px}
.card h3{margin-top:22px;font-family:var(--display);font-weight:400;font-size:16px;color:var(--leaf);text-transform:uppercase;letter-spacing:.5px}
.card p{margin:10px auto 0;width:170px;font-size:9px;line-height:13px;font-style:italic;color:var(--muted)}
.card svg{margin-top:14px}
.listings .more{position:absolute;top:440px;left:523px;width:152px;height:38px;line-height:38px}

/* sell */
.sell{height:348px;color:var(--white);padding-top:40px}
.sell-photo{position:absolute;inset:0;background:linear-gradient(180deg,#2f5f86 0%,#4f87b0 30%,#7da5bf 55%,#8a8273 75%,#6d5a45 100%)}
.sell-shade{position:absolute;inset:0;background:rgba(10,40,70,.35)}
.sell .inner{position:relative}
.sell .lede{width:810px;margin:32px auto 0}
.sell .btn{display:block;margin:26px auto 0;width:152px;height:36px;line-height:34px}

/* videos */
.videos{height:574px;padding-top:40px;color:#555}
.video-frame{position:absolute;top:121px;left:262px;width:673px;height:399px;background:linear-gradient(135deg,#3c3d3f 0%,#7a6a5c 40%,#c9a886 60%,#4a4a4c 100%)}
.play{position:absolute;left:302px;top:165px}

/* team */
.team{height:440px;background:var(--mist);padding-top:42px;color:#555}
.members{position:absolute;top:128px;left:200px;display:flex;gap:22px}
.member{width:388px;height:262px;background:var(--white);display:flex}
.member-photo{width:177px;height:262px}
.member-bio{flex:1;text-align:center;padding:22px 18px 0}
.member-bio h3{font-family:var(--display);font-weight:400;font-size:16px;color:var(--leaf);text-transform:uppercase}
.member-bio p{margin-top:10px;font-size:8.6px;line-height:13px;font-style:italic;color:var(--muted)}
.member-bio .btn{margin-top:12px;width:150px;height:38px;line-height:38px}

/* testimonials */
.voices{height:397px;color:var(--white);padding-top:38px}
.voices-photo{position:absolute;inset:0;background:linear-gradient(180deg,#4a4f5e 0%,#8a6a5a 35%,#d08a4a 55%,#6a4a3a 75%,#2f2a2c 100%)}
.voices-shade{position:absolute;inset:0;background:rgba(20,20,30,.3)}
.voices .inner{position:relative}
.quote{position:absolute;top:120px;width:330px;text-align:center}
.avatar{width:96px;height:96px;border-radius:50%;border:4px solid var(--white);margin:0 auto}
.quote h4{margin-top:14px;font-family:var(--display);font-weight:600;font-size:13px;color:var(--leaf);text-transform:uppercase;letter-spacing:.5px}
.quote small{display:block;margin-top:4px;font-size:8.5px;text-transform:uppercase}
.quote p{margin-top:12px;font-size:9px;line-height:14px}
.arrow{position:absolute;top:214px}

/* subscribe */
.subscribe{height:184px;background:var(--leaf);color:var(--white);padding-top:36px}
.signup{position:absolute;top:107px;left:431px;display:flex}
.signup .field{width:246px;height:41px;background:var(--white);font-size:9px;color:#aaa;line-height:41px;padding-left:16px;text-transform:uppercase}
.signup .send{width:90px;height:41px;background:#dcdcdc;font-size:9px;color:#888;line-height:41px;text-align:center;text-transform:uppercase}

/* partners */
.partners{height:101px;border-bottom:1px solid #e6e6e6;display:flex;justify-content:center;align-items:center;gap:56px}
.partner{width:64px;height:32px;background:#dcdcdc;border-radius:3px}
.partner.round{width:42px;height:42px;border-radius:50%}

/* footer */
.footer{height:118px;text-align:center}
.social{position:absolute;top:20px;left:559px;display:flex;gap:7px}
.social i{width:24px;height:24px;border-radius:50%;background:#666}
.footer-links{position:absolute;top:64px;width:100%;font-size:9.5px;color:#666}
.footer-links span{margin:0 7px}
.copyright{position:absolute;top:83px;width:100%;font-size:9px;color:#888}
.copyright b{font-weight:400;color:var(--ocean)}
</style>
</head>
<body>

<header class="hero">
  <div class="hero-photo" role="img" aria-label="Photo of seaside residential buildings with flowering gardens in front"></div>
  <nav class="nav">
    <a style="left:220px">Home</a>
    <a style="left:274px">Featured Listing</a>
    <a style="left:390px">Previously Sold</a>
    <a style="left:713px">Sell</a>
    <a style="left:758px">Property Search</a>
    <a style="left:876px">Team</a>
    <a style="left:926px">+ More</a>
  </nav>
  <div class="brand">Marwick<br>on the Shore</div>
  <div class="dropdown">
    <span>Team</span><span>Videos</span><span>Blog</span><span style="border:0">Explore O.C.</span>
  </div>
  <h1 class="hero-line">List with the Leader</h1>
  <div class="hero-actions">
    <a class="btn btn-green">Sell Your Home</a>
    <a class="btn btn-blue">Buy Your Home</a>
  </div>
  <div class="dots"><i></i><i class="on"></i><i></i></div>
</header>

<section class="welcome">
  <h2 class="section-title">Welcome to Marwick on the Shore</h2>
  <div class="title-rule"></div>
  <p class="lede">Lorem ipsum dolor sit amet, consectetur adipiscing elit. Pellentesque sagittis nibh sit amet lorem ipsum tempor aliquam. In rhoncus tortor quis nunc finibus faucibus. Donec cursus, tortor eu efficitur mollis, lorem ante cursus nunc, tincidunt laoreet mi elit eget orci. Sed in efficitur augue, nec laoreet purus. Donec porta venenatis dui vel ultrices. Etiam porttitor lobortis lectus, quis aliquam ex viverra non.</p>
  <a class="btn btn-ghost">Sell Your Home</a>
</section>

<section class="listings">
  <div class="tabs"><span class="tab active">Featured Listings</span><span class="tab">Previously Sold</span></div>
  <div class="cards">
    <article class="card">
      <div class="card-photo" role="img" aria-label="Photo of white high-rise apartment towers" style="background:linear-gradient(180deg,#9cc3e4,#d9dde0 55%,#6f8f5a)"></div>
      <h3>Project Name</h3>
      <p>Lorem ipsum dolor sit amet, consectetur adipiscing elit. Proin sagittis</p>
      <svg width="34" height="10" viewBox="0 0 34 10"><path d="M0 5h32M27 1l5 4-5 4" fill="none" stroke="#6cc52b" stroke-width="1.4"/></svg>
    </article>
    <article class="card">
      <div class="card-photo" role="img" aria-label="Photo of a golden residential tower against blue sky" style="background:linear-gradient(160deg,#2f6fc0,#7fb0e0 45%,#d9a653 70%,#b07a34)"></div>
      <h3>Project Name</h3>
      <p>Lorem ipsum dolor sit amet, consectetur adipiscing elit. Proin sagittis</p>
      <svg width="34" height="10" viewBox="0 0 34 10"><path d="M0 5h32M27 1l5 4-5 4" fill="none" stroke="#6cc52b" stroke-width="1.4"/></svg>
    </article>
    <article class="card">
      <div class="card-photo" role="img" aria-label="Photo of a lit hotel building at dusk" style="background:linear-gradient(180deg,#2b3d6a,#6a4a3a 50%,#c07a3a 80%,#3a2a22)"></div>
      <h3>Project Name</h3>
      <p>Lorem ipsum dolor sit amet, consectetur adipiscing elit. Proin sagittis</p>
      <svg width="34" height="10" viewBox="0 0 34 10"><path d="M0 5h32M27 1l5 4-5 4" fill="none" stroke="#6cc52b" stroke-width="1.4"/></svg>
    </article>
  </div>
  <a class="btn btn-green more">See More Listing</a>
</section>

<section class="sell">
  <div class="sell-photo" role="img" aria-label="Photo of a beach with a parasol and two lounge chairs by the sea"></div>
  <div class="sell-shade"></div>
  <div class="inner">
    <h2 class="section-title">Sell</h2>
    <div class="title-rule"></div>
    <p class="lede">Lorem ipsum dolor sit amet, consectetur adipiscing elit. In pharetra vehicula nulla id eleifend. Donec sagittis vitae turpis a finibus. Aenean dapibus vestibulum elit sed euismod. Aliquam sit amet laoreet ante. Aenean porta lacus sit amet sagittis vehicula. Suspendisse suscipit orci at enim efficitur, eu tempus ligula congue. Sed ac sodales nulla. In velit lorem, maximus at blandit at, faucibus eu enim. Pellentesque finibus in mauris et tincidunt. Praesent nulla ipsum, accumsan sed pulvinar eu, rutrum at ante. Nunc pharetra arcu eu nisl tincidunt, id pretium libero convallis. Duis et enim sit amet neque congue consequat. Mauris nec elementum justo.</p>
    <a class="btn btn-ghost">Read More</a>
  </div>
</section>

<section class="videos">
  <h2 class="section-title">Featured Videos</h2>
  <div class="title-rule"></div>
  <div class="video-frame" role="img" aria-label="Video still of two agents showing documents to a client">
    <svg class="play" width="70" height="70" viewBox="0 0 70 70"><circle cx="35" cy="35" r="35" fill="#fff"/><path d="M28 22l20 13-20 13z" fill="#6cc52b"/></svg>
  </div>
</section>

<section class="team">
  <h2 class="section-title">Meet the Team</h2>
  <div class="title-rule"></div>
  <div class="members">
    <article class="member">
      <div class="member-photo" role="img" aria-label="Portrait of team member Hal Brenner in a grey suit" style="background:linear-gradient(180deg,#9a7c5e,#6d6a68 50%,#4a4a4e)"></div>
      <div class="member-bio">
        <h3>Hal Brenner</h3>
        <p>Lorem ipsum dolor sit amet, consectetur adipiscing elit. In pharetra vehicula nulla id eleifend. Donec sagittis vitae turpis a finibus. Aenean dapibus vestibulum elit sed euismod. Aliquam sit amet laoreet ante. Aenean porta lacus sit amet sagittis vehicula. Suspendisse suscipit orci at enim efficitur, eu tempus ligula congue. Sed ac sodales nulla.</p>
        <a class="btn btn-green">Read More</a>
      </div>
    </article>
    <article class="member">
      <div class="member-photo" role="img" aria-label="Portrait of team member Nora Wells in a light jacket" style="background:linear-gradient(180deg,#5a7fa8,#c9ab8a 55%,#e3cdb4)"></div>
      <div class="member-bio">
        <h3>Nora Wells</h3>
        <p>Lorem ipsum dolor sit amet, consectetur adipiscing elit. In pharetra vehicula nulla id eleifend. Donec sagittis vitae turpis a finibus. Aenean dapibus vestibulum elit sed euismod. Aliquam sit amet laoreet ante. Aenean porta lacus sit amet sagittis vehicula. Suspendisse suscipit orci at enim efficitur, eu tempus ligula congue. Sed ac sodales nulla.</p>
        <a class="btn btn-green">Read More</a>
      </div>
    </article>
  </div>
</section>

<section class="voices">
  <div class="voices-photo" role="img" aria-label="Photo of a sunset over the ocean with palm silhouettes"></div>
  <div class="voices-shade"></div>
  <div class="inner">
    <h2 class="section-title">What Our Client Speak About Us</h2>
    <div class="title-rule"></div>
  </div>
  <svg class="arrow" style="left:208px" width="24" height="34" viewBox="0 0 24 34"><path d="M19 3L5 17l14 14" fill="none" stroke="#fff" stroke-width="3"/></svg>
  <svg class="arrow" style="left:966px" width="24" height="34" viewBox="0 0 24 34"><path d="M5 3l14 14L5 31" fill="none" stroke="#fff" stroke-width="3"/></svg>
  <div class="quote" style="left:252px">
    <div class="avatar" role="img" aria-label="Portrait of client Owen Tate" style="background:linear-gradient(180deg,#d9d4cc,#8a6a55)"></div>
    <h4>Owen Tate</h4>
    <small>A Harbor View Co.</small>
    <p>Ut id erat quis magna faucibus molestie non vel ligula. Etiam non viverra tortor, sit amet ullamcorper dolor. Sed suscipit consectetur nulla laoreet suscipit. Duis et erat non lacus sagittis pharetra sed in orci. In hac habitasse platea dictumst. Aenean sagittis leo mauris.</p>
  </div>
  <div class="quote" style="left:616px">
    <div class="avatar" role="img" aria-label="Portrait of client Rhea Moss" style="background:linear-gradient(180deg,#e6e2dc,#b08a70)"></div>
    <h4>Rhea Moss</h4>
    <small>A Harbor View Co.</small>
    <p>Ut id erat quis magna faucibus molestie non vel ligula. Etiam non viverra tortor, sit amet ullamcorper dolor. Sed suscipit consectetur nulla laoreet suscipit. Duis et erat non lacus sagittis pharetra sed in orci. In hac habitasse platea dictumst. Aenean sagittis leo mauris.</p>
  </div>
</section>

<section class="subscribe">
  <h2 class="section-title">Subscribe to Our Newletter</h2>
  <div class="title-rule"></div>
  <div class="signup"><div class="field">Enter your email id</div><div class="send">Subscribe</div></div>
</section>

<section class="partners">
  <div class="partner"></div>
  <div class="partner"></div>
  <div class="partner"></div>
  <div class="partner"></div>
  <div class="partner round"></div>
</section>

<footer class="footer">
  <div class="social"><i></i><i></i><i></i></div>
  <div class="footer-links"><span>Home</span><span>Featured Listing</span><span>Previously Sold</span><span>Sell</span><span>Property Search</span><span>Team</span><span>Videos</span><span>Blog</span><span>Explore O.C</span><span>Contact</span></div>
  <div class="copyright">Copyright © 2015 <b>Marwick on the Shore</b>. All Rights Reserved.</div>
</footer>

</body>
</html>
```